Business Card Design Project - Customized Posters

The project is to design a business card for a new web based company, that designs customized posters celebrating all types of special occasions including birthdays, weddings, new born babys, special memories etc.

You are free to design whatever you want - the only stipulation is the card truly reflects our website and our products. It's preferable that the logo is included (though not essential) and there will be one name and telephone number on the card (use A.N.Other as the name and 0123 456789 as the number) as well as our website address and email. The card should be double sided.

Our website is www.copperwrenprints.com.au - you will get a complete picture of what we do and hopefully plenty of inspiration for the business card!

Any questions please email sales@copperwrenprints.com.au and I'll respond asap. Thanks and good luck!

Target Market(s)

Everyone that would be interested in buying one of our posters!

Industry/Entity Type

Business

Requirements
Must have
• Our website address
Our email address
One name and telephone number
Nice to have
• Our logo
Should not have
• Physical address

```html
<!DOCTYPE html>
<html lang="en">
<head>
<meta charset="utf-8">
<title>Copper Wren Prints – Business Card</title>
<link rel="stylesheet" href="https://fonts.googleapis.com/css2?family=Orbitron:wght@700;800&display=swap">
<style>
  :root {
    --stage: #3c3c3c;
    --card-light: #2e2e2e;
    --card-dark: #0d0d0d;
    --purple: #8c2f8f;
    --green: #00ac4e;
    --navy: #2e2a78;
    --red: #ed1c24;
    --orange: #f58a1f;
    --sky: #2eaee3;
    --white: #ffffff;
  }
  html, body {
    margin: 0;
    width: 1200px;
    height: 908px;
    overflow: hidden;
    background: var(--stage);
  }
  .canvas {
    position: relative;
    width: 1200px;
    height: 908px;
  }
  .card {
    position: absolute;
    top: 167px;
    width: 328px;
    height: 573px;
    box-shadow: 0 8px 22px rgba(0,0,0,0.45);
  }
  .card--front { left: 235px; }
  .card--back  { left: 663px; }
  .card text {
    font-family: "Orbitron", sans-serif;
    font-weight: 700;
    fill: var(--white);
  }
  .brand-name { font-size: 21px; }
  .wordmark { font-size: 15px; fill: var(--green) !important; }
  .contact { font-size: 10.5px; }
  .contact .label { font-size: 8px; }
  .card .slogan text { font-weight: 800; font-size: 27px; }
  .card .slogan .slogan--accent { fill: var(--sky); font-style: italic; }
  .card .slogan .slogan--small { font-size: 20px; }
  .site-url { font-size: 13px; }
</style>
</head>
<body>
<main class="canvas">

  <svg class="card card--front" viewBox="0 0 289 505" role="group" aria-label="Business card front">
    <defs>
      <radialGradient id="frontShade" cx="50%" cy="50%" r="70%">
        <stop offset="0" stop-color="var(--card-light)"/>
        <stop offset="1" stop-color="var(--card-dark)"/>
      </radialGradient>
      <linearGradient id="frontBands" x1="0" y1="0" x2="1" y2="0">
        <stop offset="0"    stop-color="var(--purple)"/>
        <stop offset="0.3"  stop-color="var(--green)"/>
        <stop offset="0.5"  stop-color="var(--navy)"/>
        <stop offset="0.7"  stop-color="var(--red)"/>
        <stop offset="1"    stop-color="var(--orange)"/>
      </linearGradient>
    </defs>
    <rect width="289" height="505" fill="url(#frontShade)"/>

    <rect class="band band--top" x="46" y="0" width="199" height="100" fill="url(#frontBands)"
          role="img" aria-label="Decorative multicolour stripe pattern"/>

    <g class="brand-block">
      <rect x="46" y="150" width="20" height="20" fill="var(--white)"/>
      <text class="brand-name" x="74" y="169">COPPER</text>
      <text class="brand-name" x="46" y="201">WREN</text>
      <text class="brand-name" x="46" y="233">PRINTS</text>
    </g>

    <rect class="band band--middle" x="46" y="268" width="199" height="57" fill="url(#frontBands)"
          role="img" aria-label="Decorative multicolour stripe pattern"/>

    <text class="wordmark" x="144.5" y="356" text-anchor="middle" textLength="200" lengthAdjust="spacingAndGlyphs">COPPERWRENPRINTS</text>

    <g class="contact" text-anchor="middle">
      <text x="150" y="382" textLength="168" lengthAdjust="spacingAndGlyphs"><tspan class="label">phone: </tspan>123 456 7890</text>
      <text x="144.5" y="401" textLength="240" lengthAdjust="spacingAndGlyphs"><tspan class="label">email: </tspan>info@copperwrenprints.com.au</text>
      <text x="144.5" y="420" textLength="232" lengthAdjust="spacingAndGlyphs"><tspan class="label">web: </tspan>www.copperwrenprints.com.au</text>
    </g>

    <rect class="band band--bottom" x="46" y="440" width="199" height="65" fill="url(#frontBands)"
          role="img" aria-label="Decorative multicolour stripe pattern"/>
  </svg>

  <svg class="card card--back" viewBox="0 0 289 505" role="group" aria-label="Business card back">
    <defs>
      <radialGradient id="backShade" cx="50%" cy="50%" r="70%">
        <stop offset="0" stop-color="var(--card-light)"/>
        <stop offset="1" stop-color="var(--card-dark)"/>
      </radialGradient>
      <linearGradient id="backBands" x1="0" y1="0" x2="1" y2="0">
        <stop offset="0"   stop-color="var(--orange)"/>
        <stop offset="0.3" stop-color="var(--red)"/>
        <stop offset="0.5" stop-color="var(--navy)"/>
        <stop offset="0.7" stop-color="var(--green)"/>
        <stop offset="1"   stop-color="var(--purple)"/>
      </linearGradient>
    </defs>
    <rect width="289" height="505" fill="url(#backShade)"/>

    <rect class="band band--top" x="46" y="0" width="199" height="92" fill="url(#backBands)"
          role="img" aria-label="Decorative multicolour stripe pattern"/>

    <g class="slogan" text-anchor="middle">
      <text x="144.5" y="123" textLength="232" lengthAdjust="spacingAndGlyphs">COPPER WREN</text>
      <text x="144.5" y="156" textLength="80" lengthAdjust="spacingAndGlyphs">THE</text>
      <text class="slogan--accent" x="144.5" y="187" textLength="245" lengthAdjust="spacingAndGlyphs">PERFECT GIFT</text>
      <text x="144.5" y="218" textLength="94" lengthAdjust="spacingAndGlyphs">IDEA</text>
      <text class="slogan--small" x="144.5" y="243" textLength="127" lengthAdjust="spacingAndGlyphs">FOR ANY</text>
      <text x="144.5" y="278" textLength="221" lengthAdjust="spacingAndGlyphs">OCCASION!</text>
    </g>

    <rect class="band band--middle" x="46" y="288" width="199" height="97" fill="url(#backBands)"
          role="img" aria-label="Decorative multicolour stripe pattern"/>

    <text class="site-url" x="144.5" y="408" text-anchor="middle" textLength="258" lengthAdjust="spacingAndGlyphs">www.copperwrenprints.com.au</text>

    <rect class="band band--bottom" x="46" y="420" width="199" height="85" fill="url(#backBands)"
          role="img" aria-label="Decorative multicolour stripe pattern"/>
  </svg>

</main>
</body>
</html>
```